Hollow Thicket, a 3d voxel survival video game needs a card for gaming conventions

I am the lead developer for Hollow Thicket http://www.HollowThicket.example and need a business card to hand out at an indie gaming convention
The card would need to include the game name, website url, my name, position (Lead Developer), e-mail and phone number
The game is a 3d, voxel (with smooth terrain) based survival game with guns and wildlife. The main icon of the game would likely be a grizzly bear but I am willing to accept other designs too.
Attached is a media kit for the game with some images you can use but don't have to its just what little art I can provide. Anything on the website or from the video game can also be used. unrelated art can also be used.
Target Market(s)
Indie Developers/publishers at conferences
Industry/Entity Type
Games
Contact Information for Business Card
Name: Corin Waldrick
Position: Lead Developer
E-mail: Pale_Kettle@mailbox.example
Phone number: 555-372-1186

```html
<!DOCTYPE html>
<html lang="en">
<head>
<meta charset="utf-8">
<title>Hollow Thicket — Business Card</title>
<link href="https://fonts.googleapis.com/css2?family=Saira+Semi+Condensed:wght@500;700&family=Roboto:wght@400;500&display=swap" rel="stylesheet">
<style>
  :root {
    --stage: #a9a7a8;
    --front-bg: #1f1f20;
    --back-edge: #4f4d34;
    --back-mid: #8d8966;
    --back-glow: #d6d0b4;
    --brand-front: #b8a777;
    --brand-back: #6e5632;
    --name: #ffffff;
    --role: #5c5236;
    --contact: #f7f4ea;
    --icon: #f0ecdb;
    --bear-dark: #3a2a1c;
    --bear-mid: #6e4a2e;
    --bear-light: #a37a55;
  }
  * { margin: 0; padding: 0; box-sizing: border-box; }
  html, body {
    width: 1200px; height: 1200px; overflow: hidden;
    background: var(--stage);
  }
  .canvas { position: relative; width: 1200px; height: 1200px; }

  .card { position: absolute; overflow: hidden; }

  /* Front */
  .card-front {
    left: 237px; top: 118px; width: 715px; height: 420px;
    background: var(--front-bg);
  }
  .front-bear {
    position: absolute; left: 218px; top: 52px; width: 180px; height: 168px;
    border-radius: 46% 46% 10% 10%;
    background: radial-gradient(ellipse at 50% 40%, var(--bear-light), var(--bear-mid) 55%, var(--bear-dark) 100%);
  }
  .front-brand {
    position: absolute; left: 158px; top: 222px; width: 420px;
    font-family: "Saira Semi Condensed", sans-serif; font-weight: 700;
    font-size: 62px; line-height: 62px; letter-spacing: 3px;
    color: var(--brand-front); text-align: center; text-transform: uppercase;
  }

  /* Back */
  .card-back {
    left: 230px; top: 643px; width: 713px; height: 422px;
    background: radial-gradient(ellipse 70% 75% at 58% 48%, var(--back-glow) 0%, var(--back-mid) 55%, var(--back-edge) 100%);
  }
  .back-bear {
    position: absolute; left: 0; top: 68px; width: 292px; height: 354px;
    border-radius: 40% 50% 0 0;
    background: linear-gradient(160deg, var(--bear-light), var(--bear-mid) 55%, var(--bear-dark));
  }
  .back-brand {
    position: absolute; right: 38px; top: 46px;
    font-family: "Saira Semi Condensed", sans-serif; font-weight: 700;
    font-size: 36px; letter-spacing: 2px; text-transform: uppercase;
    color: var(--brand-back);
  }
  .person { position: absolute; right: 43px; top: 136px; text-align: right; }
  .person-name {
    font-family: "Saira Semi Condensed", sans-serif; font-weight: 500;
    font-size: 28px; line-height: 34px; color: var(--name);
  }
  .person-role {
    font-family: "Roboto", sans-serif; font-weight: 500;
    font-size: 16px; line-height: 24px; color: var(--role);
  }
  .contacts {
    position: absolute; right: 43px; top: 308px; list-style: none;
    font-family: "Roboto", sans-serif; font-size: 17px; color: var(--contact);
  }
  .contacts li {
    display: flex; align-items: center; justify-content: flex-end;
    height: 25px; gap: 16px;
  }
  .contacts svg { width: 16px; height: 16px; flex: none; }
</style>
</head>
<body>
<main class="canvas">

  <section class="card card-front">
    <div class="front-bear" role="img" aria-label="Photo of a roaring grizzly bear"></div>
    <div class="front-brand">Hollow<br>Thicket</div>
  </section>

  <section class="card card-back">
    <div class="back-bear" role="img" aria-label="Photo of a brown bear standing on a rock"></div>
    <div class="back-brand">Hollow Thicket</div>
    <div class="person">
      <div class="person-name">Corin Waldrick</div>
      <div class="person-role">Lead Developer</div>
    </div>
    <ul class="contacts">
      <li>555-372-1186
        <svg viewBox="0 0 16 16" aria-hidden="true"><path fill="var(--icon)" d="M2 6c0-2 2.5-3.5 6-3.5S14 4 14 6v1h-3V5.5H5V7H2zM4 8h8l2 5H2z"/><circle cx="8" cy="10.5" r="1.5" fill="var(--back-mid)"/></svg>
      </li>
      <li>www.hollowthicket.example
        <svg viewBox="0 0 16 16" aria-hidden="true"><g fill="none" stroke="var(--icon)" stroke-width="1.3"><circle cx="8" cy="8" r="6.3"/><ellipse cx="8" cy="8" rx="2.8" ry="6.3"/><path d="M1.7 8h12.6M2.8 4.8h10.4M2.8 11.2h10.4"/></g></svg>
      </li>
      <li>Pale_Kettle@mailbox.example
        <svg viewBox="0 0 16 16" aria-hidden="true"><rect x="1.5" y="3.5" width="13" height="9" fill="var(--icon)"/><path d="M1.5 3.5 8 9l6.5-5.5M1.5 12.5 6 8M14.5 12.5 10 8" fill="none" stroke="var(--back-mid)" stroke-width="1"/></svg>
      </li>
    </ul>
  </section>

</main>
</body>
</html>
```